Web page design for a startup, no coding

Quorvix is a Data mining startup helping companies get data from websites. We’re looking to revamp our website to make it more professional and conversation friendly.
I need a designer to design the website in PSD and Once the PSD is done, the HTML design will be awarded as a separate job. We’ll need continues improvements to the design based on the user behaviour in the site and this can be a long term work for the right designer.
Read the details on the attached document
Target Market(s)
Big data, Data Mining
Industry/Entity Type
Business Software
Number of Pages Required
5+ page
Requirements
Must have
- Refer to the doc
Nice to have
- Refer to the doc
Should not have
- Refer to the doc

```html
<!DOCTYPE html>
<html lang="en">
<head>
<meta charset="utf-8">
<title>Quorvix – Turn Websites Into Structured Data Feeds</title>
<link rel="stylesheet" href="https://fonts.googleapis.com/css2?family=Mulish:wght@400;500;600;700&family=Open+Sans:wght@400;600&display=swap">
<style>
:root{
  --orange:#ffb400;
  --orange-deep:#ffa800;
  --orange-light:#ffc940;
  --ink:#1c1c1c;
  --text:#555;
  --muted:#8a8a8a;
  --grey-band:#f2f2f2;
  --hex-grey:#7b7b7b;
  --white:#fff;
  --line:#d9d9d9;
}
*{box-sizing:border-box;margin:0;padding:0}
html,body{width:1200px;height:2707px;overflow:hidden;background:var(--white)}
body{position:relative;font-family:"Open Sans",Arial,sans-serif;color:var(--text)}
.abs{position:absolute}
.heading{font-family:"Mulish",Arial,sans-serif}

/* Hero */
.hero{position:absolute;left:0;top:0;width:1200px;height:600px}
.hero-art{position:absolute;inset:0;width:1200px;height:600px}
.brand{position:absolute;left:159px;top:44px;font-family:"Mulish",Arial,sans-serif;font-weight:600;font-size:38px;color:var(--white);letter-spacing:.5px}
.nav{position:absolute;top:50px;left:599px;display:flex;gap:30px;font-family:"Mulish",Arial,sans-serif;font-weight:700;font-size:18px;color:var(--white)}
.hero-title{position:absolute;top:222px;left:0;width:1200px;text-align:center;font-family:"Mulish",Arial,sans-serif;font-weight:600;font-size:37px;color:var(--white)}
.hero-sub{position:absolute;top:280px;left:0;width:1200px;text-align:center;font-family:"Mulish",Arial,sans-serif;font-size:20px;line-height:28px;color:var(--white)}
.btn-dark{position:absolute;left:518px;top:357px;width:170px;height:44px;background:#000;color:var(--white);font-family:"Mulish",Arial,sans-serif;font-weight:600;font-size:18px;line-height:44px;text-align:center}
.dots{position:absolute;top:562px;left:561px;display:flex;gap:8px}
.dots span{width:14px;height:14px;border-radius:50%;background:var(--white)}
.dots span.ring{background:transparent;border:2px solid var(--white)}

/* Testimonials */
.section-title{position:absolute;left:0;width:1200px;text-align:center;font-family:"Mulish",Arial,sans-serif}
.testi-title{top:646px;font-size:28px;color:var(--orange)}
.portrait{position:absolute;left:260px;top:688px;width:196px;height:196px;border-radius:50%;background:radial-gradient(circle at 50% 40%,#c89a82,#7d6a62 60%,#4a4a4a)}
.quote{position:absolute;left:484px;top:708px;width:500px;font-size:14.5px;line-height:24.5px;color:var(--muted)}
.qmark{position:absolute;font-family:Georgia,serif;font-size:48px;color:#bbb;line-height:1}
.person{position:absolute;left:485px;top:824px;font-family:"Mulish",Arial,sans-serif;font-weight:600;font-size:17px;color:var(--ink)}
.role{position:absolute;left:485px;top:848px;font-size:13px;color:var(--muted)}

/* Use cases */
.usecases{position:absolute;left:0;top:944px;width:1200px;height:527px;background:var(--grey-band)}
.usecases-title{top:60px;font-size:27px;line-height:36px;color:var(--ink)}
.case{position:absolute;width:360px}
.case h3{font-family:"Mulish",Arial,sans-serif;font-weight:500;font-size:18px;color:var(--ink);margin-bottom:5px}
.case p{font-size:11.5px;line-height:17px;color:var(--muted)}
.case.left{text-align:right;left:104px}
.case.right{left:726px}
.case-icon{position:absolute;width:68px;height:68px;border-radius:50%;background:var(--white);border:2px solid #e2e2e2}
.case-icon svg{position:absolute;left:16px;top:16px;width:32px;height:32px}

/* Why us */
.why-title{top:1528px;font-size:29px;color:var(--ink)}
.hexes{position:absolute;left:151px;top:1585px;width:898px;height:242px}
.hex-text{position:absolute;top:1685px;width:200px;text-align:center;color:var(--white)}
.hex-text h4{font-family:"Mulish",Arial,sans-serif;font-weight:700;font-size:16px;margin-bottom:6px}
.hex-text p{font-size:10.5px;line-height:16px;opacity:.92}

/* Contact */
.contact{position:absolute;left:0;top:1888px;width:1200px;height:479px}
.contact-bg{position:absolute;inset:0;width:1200px;height:479px}
.contact-title{top:52px;font-size:31px;color:var(--ink)}
.contact-sub{position:absolute;top:100px;left:0;width:1200px;text-align:center;font-family:"Mulish",Arial,sans-serif;font-size:19px;line-height:29px;color:#555}
.field{position:absolute;background:var(--white);border:1px solid #cfcfcf;font-size:13px;color:#888;padding:10px 16px}
.btn-submit{position:absolute;left:534px;top:392px;width:136px;height:38px;background:var(--orange);color:var(--white);font-family:"Mulish",Arial,sans-serif;font-weight:700;font-size:14px;line-height:38px;text-align:center}

/* Footer */
.footer-col{position:absolute;top:2418px}
.footer-col h5{font-family:"Mulish",Arial,sans-serif;font-weight:500;font-size:22px;color:var(--orange);margin-bottom:10px}
.footer-col ul{list-style:none}
.footer-col li{font-size:14px;line-height:28.5px;color:#666}
.social{display:flex;gap:11px;margin-top:4px}
.social span{width:32px;height:32px;border-radius:50%;background:var(--orange)}
.footer-brand{position:absolute;left:841px;top:2428px;font-family:"Mulish",Arial,sans-serif;font-weight:500;font-size:42px;color:#9a9a9a}
.divider{position:absolute;left:159px;top:2641px;width:884px;height:1px;background:var(--line)}
.copyright{position:absolute;top:2657px;left:0;width:1200px;text-align:center;font-size:12px;color:#aaa}
</style>
</head>
<body>

<header class="hero">
  <svg class="hero-art" viewBox="0 0 1200 600" role="img" aria-label="Orange hero illustration of stacked data sheets flowing into structured feeds">
    <defs>
      <linearGradient id="heroGrad" x1="0" y1="0" x2="1" y2="1">
        <stop offset="0" stop-color="#ffb000"/>
        <stop offset=".5" stop-color="#ffbf2a"/>
        <stop offset="1" stop-color="#ffae00"/>
      </linearGradient>
    </defs>
    <polygon points="0,0 1200,0 1200,534 600,598 0,534" fill="url(#heroGrad)"/>
  </svg>
  <div class="brand">quorvix</div>
  <nav class="nav"><span>Solutions</span><span>Pricing</span><span>Company</span><span>Get free Quote</span></nav>
  <h1 class="hero-title">Turn Websites Into Structured Data feeds</h1>
  <p class="hero-sub">Easily get structured data feeds from any website through our cloud based data &nbsp;as a service<br>platform. No programming ,Servers or Expensive Softwares required</p>
  <div class="btn-dark">Get free Quote</div>
  <div class="dots"><span class="ring"></span><span></span><span></span><span></span></div>
</header>

<section>
  <h2 class="section-title testi-title">Testimonials</h2>
  <div class="portrait" role="img" aria-label="Portrait photo of the client quoted"></div>
  <span class="qmark" style="left:462px;top:700px">&ldquo;</span>
  <p class="quote">Quorvix was very responsive and quick to deliver. They were happy to do 2 iterations on the initial data scrape set up to ensure we got the info we needed moving forward. They delivered great results were others had previously failed. We're excited to have found this service and will be looking</p>
  <span class="qmark" style="left:856px;top:782px">&rdquo;</span>
  <div class="person">Mara Lindqvist</div>
  <div class="role">Director of Business Development @ Brightwell Labs</div>
</section>

<section class="usecases">
  <h2 class="section-title usecases-title">Businesses of all sizes use our clean data feeds to Quickly build apps,<br>Experiment with fresh ideas and Solve business problems</h2>

  <div class="case left" style="top:192px"><h3>ECommerce</h3><p>Our Ecommerce product data feeds gives you access<br>to structured product information like pricing,</p></div>
  <div class="case-icon" style="left:480px;top:190px"><svg viewBox="0 0 32 32" fill="none" stroke="#ffb400" stroke-width="2"><rect x="3" y="5" width="26" height="22"/><line x1="3" y1="10" x2="29" y2="10"/><path d="M9 14h3l2 7h8l2-5H13"/></svg></div>

  <div class="case left" style="top:289px"><h3>Lead Generation</h3><p>We help find quality leads for your business by<br>extracting public data from all kind of sources like</p></div>
  <div class="case-icon" style="left:480px;top:287px"><svg viewBox="0 0 32 32" fill="#ffb400"><circle cx="16" cy="9" r="5"/><circle cx="7" cy="13" r="3.5"/><circle cx="25" cy="13" r="3.5"/><path d="M8 28c0-7 3-11 8-11s8 4 8 11z"/><path d="M1 26c0-5 2-8 6-8 1 0 2 .3 2.5.7C8 21 7.5 23 7.5 26z"/><path d="M31 26c0-5-2-8-6-8-1 0-2 .3-2.5.7C24 21 24.5 23 24.5 26z"/></svg></div>

  <div class="case left" style="top:390px"><h3>SERP Tracking</h3><p>Our SERP data feeds gives companies access to<br>Search Engine rankings of any keywords from search</p></div>
  <div class="case-icon" style="left:480px;top:388px"><svg viewBox="0 0 32 32" fill="none" stroke="#ffb400" stroke-width="2"><polyline points="1,20 7,14 12,18"/><polyline points="20,14 25,18 31,10"/><circle cx="16" cy="15" r="4.5"/><line x1="13" y1="19" x2="9" y2="25"/></svg></div>

  <div class="case-icon" style="left:637px;top:190px"><svg viewBox="0 0 32 32" fill="none" stroke="#ffb400" stroke-width="2"><rect x="7" y="4" width="20" height="24"/><path d="M7 9H4v16a3 3 0 0 0 3 3"/><line x1="11" y1="10" x2="23" y2="10"/><line x1="11" y1="15" x2="23" y2="15"/><line x1="11" y1="20" x2="23" y2="20"/></svg></div>
  <div class="case right" style="top:192px"><h3>News Aggregation</h3><p>We help businesses build their own unique news<br>data feeds by aggregating data from news sites</p></div>

  <div class="case-icon" style="left:637px;top:287px"><svg viewBox="0 0 32 32" fill="none" stroke="#ffb400" stroke-width="2"><circle cx="16" cy="16" r="11"/><line x1="16" y1="1" x2="16" y2="7"/><line x1="16" y1="25" x2="16" y2="31"/><line x1="1" y1="16" x2="7" y2="16"/><line x1="25" y1="16" x2="31" y2="16"/><circle cx="16" cy="13" r="3" fill="#ffb400"/><path d="M10 22c1-4 3-5 6-5s5 1 6 5" fill="#ffb400"/></svg></div>
  <div class="case right" style="top:289px"><h3>Recruiting</h3><p>We help recruiters automate scouting candidate<br>profiles from different online sources</p></div>

  <div class="case-icon" style="left:637px;top:388px"><svg viewBox="0 0 32 32" fill="none" stroke="#ffb400" stroke-width="2"><rect x="9" y="2" width="15" height="28" rx="2"/><line x1="9" y1="7" x2="24" y2="7"/><line x1="9" y1="24" x2="24" y2="24"/></svg></div>
  <div class="case right" style="top:390px"><h3>Build your App</h3><p>We help businesses quickly build their apps on top<br>of our scalable data extraction infrastructure</p></div>
</section>

<section>
  <h2 class="section-title why-title">Why Us</h2>
  <svg class="hexes" viewBox="0 0 898 242">
    <polygon points="56,0 168,0 224,121 168,242 56,242 0,121" fill="#ffb400"/>
    <polygon points="280,0 392,0 448,121 392,242 280,242 224,121" fill="#7b7b7b"/>
    <polygon points="504,0 616,0 672,121 616,242 504,242 448,121" fill="#ffb400"/>
    <polygon points="730,0 842,0 898,121 842,242 730,242 674,121" fill="#7b7b7b"/>
    <g fill="none" stroke="#fff" stroke-width="2.5">
      <path d="M92 37h16a5 5 0 1 1 10 0h16v16a5 5 0 1 1 0 10v16h-42z"/>
      <ellipse cx="336" cy="34" rx="20" ry="7"/><path d="M316 34v34c0 4 9 7 20 7s20-3 20-7V34"/><path d="M316 46c0 4 9 7 20 7s20-3 20-7"/><path d="M316 57c0 4 9 7 20 7s20-3 20-7"/>
      <polyline points="538,30 538,72 584,72"/><polyline points="545,62 556,50 564,56 580,38"/><polyline points="572,38 580,38 580,46"/>
      <path d="M760 66c6-6 12-6 20-4h12c3 0 3 4 0 4h-10l14 0 12-8c3-2 6 1 3 4l-14 12h-30"/>
      <line x1="770" y1="28" x2="802" y2="28" stroke-dasharray="3 3"/><line x1="770" y1="38" x2="802" y2="38" stroke-dasharray="3 3"/><line x1="770" y1="48" x2="802" y2="48" stroke-dasharray="3 3"/>
    </g>
  </svg>
  <div class="hex-text" style="left:163px"><h4>Solve Real Problems</h4><p>Quorvix provides a fully managed Big Data As A Service. You can easily plug our data feeds into your favourite</p></div>
  <div class="hex-text" style="left:387px"><h4>Clean Data</h4><p>We follow a strict quality assurance process and a Machine learning based Q&amp;A system to ensure the</p></div>
  <div class="hex-text" style="left:611px"><h4>Customer Success</h4><p>Ensuring Customer success is our first priority. Our customer success team consists of experienced</p></div>
  <div class="hex-text" style="left:833px;width:206px"><h4>Data Wrangling Support</h4><p>Quorvix helps those who need data wrangling support by providing profiling, filtering</p></div>
</section>

<section class="contact">
  <svg class="contact-bg" viewBox="0 0 1200 479" role="img" aria-label="Photo of a white desk with keyboard, mouse, notebook and coffee cup">
    <defs>
      <linearGradient id="deskGrad" x1="0" y1="0" x2="1" y2="1">
        <stop offset="0" stop-color="#e9eaec"/>
        <stop offset=".5" stop-color="#f4f5f6"/>
        <stop offset="1" stop-color="#e2e3e5"/>
      </linearGradient>
    </defs>
    <rect width="1200" height="479" fill="url(#deskGrad)"/>
  </svg>
  <h2 class="section-title contact-title">We're here to help!</h2>
  <p class="contact-sub">We're friendly and available to help solve your data extraction problems.<br>Fill the form below to contact us. Let us do the heavy lifting for youa</p>
  <div class="field" style="left:292px;top:191px;width:378px;height:40px">Email address</div>
  <div class="field" style="left:677px;top:191px;width:233px;height:40px">Your Monthly Budget</div>
  <div class="field" style="left:292px;top:242px;width:618px;height:130px">Your Message</div>
  <div class="btn-submit">SUBMIT</div>
</section>

<footer>
  <div class="footer-col" style="left:157px"><h5>Quick Links</h5><ul><li>Blog</li><li>Answers</li><li>Case Studies</li><li>Slide</li></ul></div>
  <div class="footer-col" style="left:379px"><h5>Resources</h5><ul><li>Startup Partner program</li><li>FAQ</li><li>Careers</li></ul></div>
  <div class="footer-col" style="left:616px"><h5>Follow Us</h5><div class="social"><span></span><span></span><span></span><span></span></div></div>
  <div class="footer-brand">quorvix</div>
  <div class="divider"></div>
  <p class="copyright">© 2016 Company Name &nbsp;All right reserved &nbsp;Term of Use</p>
</footer>

</body>
</html>
```